Lumen Fitness Personal Training Business

I need a business card design with a logo for my personal training company. I'd like the colors to be a vibrant green and black. I'd like the logo to incorporate an anvil (or something similar). I train hardcore competitive athletes as well as soccer moms trying to get and/or stay in shape. I need a logo that will not pigeon hole me in one category or the other, but at the same time not be too intimidating to soccer moms, but will not be off putting to the more hardcore trainees. The design should be attention grabbing and aesthetic.
Target Market(s)
Hardcore athletes as well as average people just trying to get/stay in shape.
Industry/Entity Type
Training

```html
<!DOCTYPE html>
<html lang="en">
<head>
<meta charset="UTF-8">
<title>Lumen Fitness – Business Card</title>
<link href="https://fonts.googleapis.com/css2?family=Open+Sans:wght@400;600;700&display=swap" rel="stylesheet">
<style>
  :root {
    --page-bg: #e9e9e6;
    --card-dark: #161816;
    --card-light: #ffffff;
    --brand-green: #2fb24a;
    --brand-lime: #7ccf2e;
    --text-ink: #1b1d1b;
    --text-grey: #6c706c;
    --text-white: #f3f5f3;
  }
  * { margin: 0; padding: 0; box-sizing: border-box; }
  html, body {
    width: 1200px;
    height: 1200px;
    overflow: hidden;
    background: var(--page-bg);
    font-family: "Open Sans", Arial, sans-serif;
  }
  .canvas {
    position: relative;
    width: 1200px;
    height: 1200px;
  }
  .card {
    position: absolute;
    left: 150px;
    width: 900px;
    height: 514px;
    box-shadow: 0 10px 28px rgba(0,0,0,0.2);
    overflow: hidden;
  }

  /* Front */
  .card-front {
    top: 60px;
    background: var(--card-dark);
    display: flex;
    flex-direction: column;
    align-items: center;
    justify-content: center;
    gap: 28px;
  }
  .front-mark {
    width: 56px;
    height: 56px;
    background: var(--brand-green);
  }
  .front-name {
    color: var(--text-white);
    font-weight: 600;
    font-size: 62px;
    letter-spacing: 6px;
    text-transform: uppercase;
  }

  /* Back */
  .card-back {
    top: 626px;
    background: var(--card-light);
  }
  .back-brand {
    position: absolute;
    left: 58px;
    top: 54px;
    display: flex;
    align-items: center;
    gap: 12px;
  }
  .back-brand-mark {
    width: 22px;
    height: 22px;
    background: var(--brand-green);
  }
  .back-brand-name {
    color: var(--brand-green);
    font-weight: 600;
    font-size: 30px;
    letter-spacing: 2px;
    text-transform: uppercase;
  }
  .contact {
    position: absolute;
    left: 58px;
    top: 170px;
    color: var(--text-grey);
    font-size: 19px;
    line-height: 27px;
  }
  .contact-address { margin-bottom: 10px; }
  .contact-label {
    color: var(--brand-green);
    font-weight: 600;
  }
  .person {
    position: absolute;
    left: 564px;
    top: 250px;
  }
  .person-name {
    color: var(--text-ink);
    font-weight: 700;
    font-size: 34px;
    line-height: 42px;
  }
  .person-title {
    color: var(--text-grey);
    font-size: 21px;
  }
  .band {
    position: absolute;
    left: 0;
    bottom: 0;
    width: 900px;
    height: 112px;
  }
</style>
</head>
<body>
  <main class="canvas">
    <section class="card card-front">
      <div class="front-mark"></div>
      <div class="front-name">Lumen Fitness</div>
    </section>

    <section class="card card-back">
      <div class="back-brand">
        <div class="back-brand-mark"></div>
        <div class="back-brand-name">Lumen Fitness</div>
      </div>

      <div class="contact">
        <p class="contact-address">48 Harbor Lane, Suite 2<br>Northvale, 204581</p>
        <p><span class="contact-label">p:</span> 021-555 0148</p>
        <p><span class="contact-label">f:</span> 021-555 0149</p>
        <p><span class="contact-label">e:</span> hello@lumenfit.com</p>
      </div>

      <div class="person">
        <p class="person-name">Daniel Reyes</p>
        <p class="person-title">Managing Director</p>
      </div>

      <svg class="band" viewBox="0 0 900 112" aria-hidden="true">
        <polygon class="band-dark" points="0,0 345,0 295,112 0,112" fill="var(--card-dark)"/>
        <polygon class="band-green" points="359,0 900,0 900,112 309,112" fill="var(--brand-green)"/>
      </svg>
    </section>
  </main>
</body>
</html>
```